Cat-products company needs smart, yet endearing, business card

We need a business card design for a new, but up-and-running, business based in Honolulu, Hawaii. The business is Purrnest Nook Co. Our first product is the most environmentally-friendly cat grass kit ever seen on the planet. Future products, currently in the R&D phase, will include a variety of exciting cat scratchers. We also do consulting work to help apartment-dwellers make their home more cat-friendly and, in the future, plan on doing full, custom installs of structure to create high walkways for cats.

Target Market(s)

Middle-aged, apartment-dwelling, middle-class workers who own 1 or more cats and who dote on them.

Industry/Entity Type

Pet Care

Contact Information for Business Card

A striking, professional, yet warm and friendly design is what we're after.

Font styles to use
Serif
Sans Serif
Other font styles liked:
• Comfortaa

Colors

Designer to choose colors to be used in the design.

Requirements
Must have
• The company logo: (see attachment)
• The company name: Purrnest Nook Co
• The web address: www.purrnestnookco.com
• Email: support@purrnestnookco.com
• Phone: +1 (808) 571 6023
• Update (Fri Jun 30 3017 7:45pm Hawaii Time) I would like, is possible, uploaded picture of the cat grass kit on the back of the card with some text along the lines of: Purrnest Nook Co - Maker Of The Leafiest Feline Sprout Set Yet
Nice to have
• A cat picture, cartoon, real or silhouette that illustrates cats in action and/or relaxing; ie using the apartment space to live, play and relax in and being well-contented.
• Most of the website is done in the font: Comfortaa. It might be nice to continue using this for brand consistency.
Should not have
• Hard-to-read fonts.

```html
<!DOCTYPE html>
<html lang="en">
<head>
<meta charset="utf-8">
<title>Purrnest Nook Co – Business Card</title>
<link rel="stylesheet" href="https://fonts.googleapis.com/css2?family=Comfortaa:wght@700&family=Fira+Sans+Condensed:wght@500&family=Questrial&display=swap">
<style>
  :root {
    --backdrop: #e4e4e4;
    --card: #f7f7f6;
    --brown: #55302a;
    --gold: #f0ac00;
    --gold-faint: #f5e6bf;
    --ink: #4a4446;
    --rule: #3d3536;
    --dot: #b9a59f;
  }
  * { margin: 0; padding: 0; box-sizing: border-box; }
  html, body { width: 1200px; height: 960px; overflow: hidden; }
  body { background: var(--backdrop); position: relative; font-family: "Questrial", sans-serif; }

  .card {
    position: absolute;
    width: 600px;
    height: 342px;
    background: var(--card);
    border-radius: 20px;
    overflow: hidden;
  }
  .card--front { left: 314px; top: 113px; }
  .card--back  { left: 311px; top: 473px; }

  .front__decor {
    position: absolute; left: -10px; top: 10px;
    width: 310px; height: 310px; border-radius: 50%;
    background: var(--gold-faint); opacity: .7;
  }

  .front__brand {
    position: absolute; right: 34px; top: 118px;
    font-family: "Comfortaa", sans-serif; font-weight: 700;
    font-size: 25px; line-height: 1.15; color: var(--brown);
    text-align: right;
  }

  .person { position: absolute; left: 33px; top: 187px; }
  .person__name {
    font-family: "Fira Sans Condensed", sans-serif; font-weight: 500;
    font-size: 24px; color: var(--brown); letter-spacing: .3px;
  }
  .person__role { font-size: 15px; color: var(--gold); margin-top: 3px; letter-spacing: .3px; }

  .front__rule {
    position: absolute; left: 33px; right: 33px; top: 244px;
    height: 1px; background: var(--rule);
  }

  .contact { position: absolute; left: 33px; top: 256px; list-style: none; }
  .contact li {
    display: flex; align-items: center; gap: 8px;
    font-size: 14.5px; color: var(--ink); height: 19.5px;
  }
  .contact svg { width: 13px; height: 13px; fill: var(--brown); flex: none; }

  .social { position: absolute; right: 33px; top: 254px; display: flex; gap: 2px; }
  .social span { width: 20px; height: 20px; border-radius: 50%; background: var(--dot); }

  .address {
    position: absolute; right: 33px; top: 278px;
    font-size: 14.5px; line-height: 19px; color: var(--ink); text-align: right;
  }

  .band { position: absolute; bottom: 0; height: 8px; }
  .band--brown { left: 0; width: 392px; background: var(--brown); }
  .band--gold  { left: 395px; right: 0; background: var(--gold); }

  .back__brand {
    position: absolute; left: 0; right: 0; top: 120px;
    display: flex; align-items: center; justify-content: center; gap: 14px;
    font-family: "Comfortaa", sans-serif; font-weight: 700;
    font-size: 34px; color: var(--brown);
  }
  .back__brand .mark { width: 34px; height: 34px; background: var(--gold); border-radius: 4px; }

  .back__web {
    position: absolute; left: 0; right: 0; top: 284px; text-align: center;
    font-family: "Comfortaa", sans-serif; font-weight: 700;
    font-size: 18px; letter-spacing: 2px; color: var(--gold);
  }
</style>
</head>
<body>

<section class="card card--front" aria-label="Business card front">
  <div class="front__decor" aria-hidden="true"></div>
  <div class="front__brand">Purrnest<br>Nook Co</div>

  <div class="person">
    <div class="person__name">LEILANI KAHO</div>
    <div class="person__role">CEO/FOUNDER</div>
  </div>

  <div class="front__rule"></div>

  <ul class="contact">
    <li>
      <svg viewBox="0 0 24 24" aria-hidden="true"><path d="M6.6 10.8a15.1 15.1 0 0 0 6.6 6.6l2.2-2.2c.3-.3.7-.4 1-.2 1.1.4 2.3.6 3.6.6.6 0 1 .4 1 1V20c0 .6-.4 1-1 1A17 17 0 0 1 3 4c0-.6.4-1 1-1h3.5c.6 0 1 .4 1 1 0 1.3.2 2.5.6 3.6.1.3 0 .7-.2 1z"/></svg>
      +1 (808) 571 6023
    </li>
    <li>
      <svg viewBox="0 0 24 24" aria-hidden="true"><path d="M2 5h20v14H2z M2 5l10 7 10-7" /><path d="M2 5h20L12 12z" fill="#f7f7f6"/></svg>
      support@purrnestnookco.com
    </li>
    <li>
      <svg viewBox="0 0 24 24" aria-hidden="true"><circle cx="12" cy="12" r="10"/><path d="M2 12h20M12 2c3 3 3 17 0 20M12 2c-3 3-3 17 0 20" stroke="#f7f7f6" stroke-width="1.6" fill="none"/></svg>
      www.purrnestnookco.com
    </li>
  </ul>

  <div class="social" aria-label="Social profiles">
    <span></span><span></span><span></span><span></span>
  </div>

  <div class="address">4120 Plumeria Way<br>Honolulu, Hawaii 96815</div>

  <div class="band band--brown"></div>
  <div class="band band--gold"></div>
</section>

<section class="card card--back" aria-label="Business card back">
  <div class="back__brand"><span class="mark" aria-hidden="true"></span>Purrnest Nook Co</div>
  <div class="back__web">PURRNESTNOOKCO.com</div>
</section>

</body>
</html>
```